Keystonery Billboard - Financial Services Company (Investments, Tax Planning and Insurance)

Our new office has a billboard directly above the office building. We'd like something eye-catching with a strong Call to Action, with the main part of the billboard being under 7 words if possible. We'd like you to include a way to get ahold of us (either our website keystoneryllc.example or our phone number 302-418-2907. You may also include in small font something to indicate that we've been serving the area since 1980 (the DE area, the tri-state area, the Marlowe Hollow, etc.)

We offer financial planning, tax planning, and insurance, and we help our clients to focus on their goals and happiness by providing everything they need for lifelong wealth under one roof.

Our logos are attached, we use a triangle logo with green and gray. We use the tagline "discover lasting prosperity" but this does not need to be included.

Potential ideas we have seen from other financial companies-
- the concept that the driver spends more time looking at billboards than planning for their retirement
-something along the lines of "everything you need for your finances is in this building right here" planning, investments, taxes, insurance"
-don't spend your time worrying about retirement, let us help you plan for it
-are you working for your money, or is it working for you?
- retirement takes planning, we're here to help
- ready to retire? talk to us
- need investment advice?
- need help investing?
- crossing your fingers isn't a retirement plan. we can help.
- retiring soon? you need help.

Those are just general ideas, please feel free to be creative.

brand colors:
#00b585
#00b185
#000000
#ffffff
#6d6f75
#6d6f75
#6f7074
#021712
#052e24

```html
<!DOCTYPE html>
<html lang="en">
<head>
<meta charset="UTF-8">
<title>Keystonery Billboard</title>
<link href="https://fonts.googleapis.com/css2?family=Montserrat:wght@500;800;900&display=swap" rel="stylesheet">
<style>
  :root {
    --brand-green: #00995c;
    --brand-gray: #6d6f75;
    --mint-light: #eef7f1;
    --mint-mid: #d7efe6;
    --mint-edge: #a9e0d3;
    --white: #ffffff;
    --stage: #e9ecef;
  }
  * { margin: 0; padding: 0; box-sizing: border-box; }
  html, body {
    width: 1200px;
    height: 900px;
    overflow: hidden;
    background: var(--stage);
    font-family: "Montserrat", sans-serif;
  }
  .billboard {
    position: absolute;
    left: 0;
    top: 193px;
    width: 1200px;
    height: 514px;
    overflow: hidden;
    background: radial-gradient(ellipse at 40% 30%, #fbfdf8 0%, var(--mint-light) 45%, var(--mint-mid) 100%);
  }
  .billboard__shapes {
    position: absolute;
    inset: 0;
  }
  .brand {
    position: absolute;
    left: 390px;
    top: 78px;
  }
  .brand__name {
    font-weight: 800;
    font-size: 66px;
    line-height: 1;
    color: var(--brand-green);
    letter-spacing: -1px;
  }
  .brand__tagline {
    margin-top: 8px;
    font-weight: 500;
    font-size: 12px;
    letter-spacing: 5px;
    color: var(--brand-gray);
    text-transform: uppercase;
  }
  .headline {
    position: absolute;
    left: 212px;
    top: 200px;
    font-weight: 900;
    font-size: 56px;
    line-height: 62px;
    letter-spacing: -0.5px;
    color: var(--brand-gray);
    text-transform: uppercase;
  }
  .headline__accent { color: var(--brand-green); }
  .headline__answer {
    display: block;
    margin-left: 8px;
    color: var(--brand-green);
  }
  .hero-photo {
    position: absolute;
    left: 782px;
    top: 160px;
    width: 418px;
    height: 285px;
    border-radius: 120px 0 0 120px;
    background: linear-gradient(100deg, #f4b3a6 0%, #ee9f8f 45%, #d9b59b 70%, #a9acb0 100%);
  }
  .cta {
    position: absolute;
    left: 0;
    top: 428px;
    height: 86px;
    width: 760px;
    display: flex;
    align-items: center;
    padding-left: 52px;
    color: var(--white);
  }
  .cta__label {
    font-weight: 900;
    font-size: 27px;
    letter-spacing: 2px;
    margin-right: 22px;
  }
  .cta__icon { width: 44px; height: 44px; margin-right: 10px; }
  .cta__phone {
    font-weight: 800;
    font-size: 36px;
    letter-spacing: -0.5px;
  }
</style>
</head>
<body>
  <main class="billboard">
    <svg class="billboard__shapes" width="1200" height="514" viewBox="0 0 1200 514" aria-hidden="true">
      <!-- right accent band -->
      <polygon points="990,0 1200,0 1200,514 764,514" fill="var(--brand-green)"/>
      <path d="M944,514 C980,400 1080,290 1200,236 L1200,514 Z" fill="var(--mint-edge)"/>
      <path d="M958,514 C995,410 1090,305 1200,254 L1200,514 Z" fill="var(--brand-gray)"/>
      <!-- bottom call bar -->
      <polygon points="0,428 739,426 703,514 0,514" fill="var(--brand-gray)"/>
      <!-- down arrow -->
      <rect x="82" y="0" width="44" height="320" fill="var(--brand-green)"/>
      <polygon points="9,280 40,250 104,314 168,250 199,280 104,375" fill="var(--brand-green)"/>
    </svg>

    <div class="brand">
      <div class="brand__name">Keystonery</div>
      <div class="brand__tagline">Discover lasting prosperity</div>
    </div>

    <h1 class="headline">
      Worrying about<br>
      your <span class="headline__accent">$$$?</span>
      <span class="headline__answer">Us too!</span>
    </h1>

    <div class="hero-photo" role="img" aria-label="Photo of an open hand holding a pink piggy bank"></div>

    <div class="cta">
      <span class="cta__label">CALL US</span>
      <svg class="cta__icon" viewBox="0 0 44 44" aria-hidden="true">
        <circle cx="22" cy="22" r="21" fill="var(--white)"/>
        <path d="M15 11c1.5-1 3-.6 3.8.8l2 3.6c.6 1.1.3 2.3-.7 3l-1.3.9c.9 2.4 2.7 4.4 5 5.6l1-1.2c.8-.9 2.1-1.1 3.1-.4l3.4 2.3c1.3.9 1.5 2.5.4 3.8l-1.5 1.7c-1.3 1.4-3.4 1.8-5.2.9C19.4 29.6 14.8 24.7 12.9 19c-.6-1.8 0-3.9 1.3-5.2z" fill="var(--brand-gray)"/>
      </svg>
      <span class="cta__phone">302-418-2907</span>
    </div>
  </main>
</body>
</html>
```